Business Card Design

I need a business card design for my new business based on Long Island, CT also serving NYC called Pawhaven Retreat. I have built a website with cardmint that can be looked at as a basis for the card. It is pawhavenretreat.com.

I board Labrador Retrievers in my home. Specialize in one breed. Cage free environment. Dogs have full run of home and fenced in property. Pawhaven Retreat is a one-of-a-kind, high-quality dog-boarding provider serving specifically Labrador Retrievers. By working with a dog I am comfortable with, I am able to offer the best care for all pets that come through my door. I work with Lab owners in the Long Island/NYC area to provide an
in-home safe, reliable and fun environment for daycare and overnight stays.

I provide a unique boarding experience for Labrador Retrievers on Long Island. Your Lab should be well mannered, housebroken and good with other dogs. Provided your pet is well mannered and house trained, my boarding services allow dogs to experience a cage-free stay while having free roam of my home and property. This allows owners a unique alternative to a kennel, giving pets the chance to experience a home away from home rather than chain linked fences and cold concrete floors.
As a guest at Pawhaven Retreat, your dog will get:

4-star kibble
Access to my in-ground pool
All-natural snack selection
Companionship of other retrievers including my two
Full run of entire home and fenced-in backyard
Photos AND videos posted to Snapgram so you can see your dog having fun while away
Toys, bones and affection

I think it is important to have a pic of the 3 colored labs below. Also the picture of my own personal labs ..the white one with the black puppy. Maybe some paw prints. If using any imagery that MUST look EXACTLY like labrador retriever no generic dogs. Thank you
Updates

The Back of the Card should have the following: The background should be one of the pictures I sent (white dog in pool or another pic I included) At Pawhaven Retreat your Lab gets: Cage Free Environment Full run of my home and fenced in yard In-ground pool Toys and affection Companionship of other Labrador Retrievers Photos and Videos posted Snapgram of your loved one FRONT OF THE CARD: should include picture of the 3 labs (yellow white brown) OR picture of white dog in pool. Pawhaven Retreat should be in larger font than the rest. the following can be in any order. Tom Pelley Elmbrook, CT in Central Long Island pawhavenretreat.com 631-555-0192

Industry/Entity Type

Environment

Contact Information for Business Card

Pawhaven Retreat
Elmbrook, CT
Tom Pelley
hello@pawhavenretreat.com
631-555-0192

```html
<!DOCTYPE html>
<html lang="en">
<head>
<meta charset="utf-8">
<title>Pawhaven Retreat — Business Card</title>
<link href="https://fonts.googleapis.com/css2?family=Arimo:wght@400;500&display=swap" rel="stylesheet">
<style>
  :root{
    --page:#e9e6e1;
    --ink:#1b1b1b;
    --card-white:#f7f7f7;
    --card-white-edge:#dcdcdc;
    --card-black:#060606;
    --rule:#cfcfcf;
    --icon:#3a3a3a;
    --text-light:#f2f2f2;
    --pup-light:#efe3c8;
    --pup-mid:#d9c49a;
  }
  *{margin:0;padding:0;box-sizing:border-box}
  html,body{width:1200px;height:858px;overflow:hidden}
  body{
    background:var(--page);
    font-family:"Arimo", Helvetica, Arial, sans-serif;
    position:relative;
  }
  .card{
    position:absolute;
    left:260px;
    width:680px;
    height:389px;
    box-shadow:0 6px 18px rgba(0,0,0,.25);
    overflow:hidden;
  }
  /* FRONT */
  .card--front{top:24px;display:flex}
  .front__info{
    width:60%;
    flex:none;
    background:linear-gradient(135deg,#ffffff 0%,var(--card-white) 60%,var(--card-white-edge) 100%);
    padding:58px 0 0 40px;
    color:var(--ink);
    position:relative;
  }
  .front__name{font-size:28px;font-weight:400;letter-spacing:-.3px;line-height:1.1;white-space:nowrap}
  .front__owner{font-size:24px;margin-top:26px;line-height:1.1;padding-left:40px}
  .front__contacts{
    position:absolute;left:40px;bottom:48px;
    list-style:none;font-size:17px;
  }
  .front__contacts li{display:flex;align-items:center;gap:12px;margin-top:10px}
  .contact-icon{width:24px;height:24px;display:block;flex:none}
  .front__photo-side{
    flex:1;background:var(--card-black);
    position:relative;
    border-left:6px solid var(--card-black);
  }
  .front__photo-side::before{
    content:"";position:absolute;left:10px;top:0;bottom:0;width:2px;background:var(--rule);
  }
  .front__photo{
    position:absolute;left:36px;top:70px;width:210px;height:250px;
    border-radius:46% 46% 40% 40%;
    background:radial-gradient(ellipse at 45% 40%,var(--pup-light) 0%,var(--pup-mid) 68%,rgba(217,196,154,0) 71%);
  }
  /* BACK */
  .card--back{
    top:445px;
    background:linear-gradient(160deg,#111 0%,var(--card-black) 55%,#000 100%);
    color:var(--text-light);
    padding:62px 0 0 54px;
  }
  .card--back::before,.card--back::after{
    content:"";position:absolute;top:0;bottom:0;width:3px;background:var(--rule);
  }
  .card--back::before{left:18px}
  .card--back::after{right:18px}
  .back__heading{font-size:22px;font-weight:400;margin-bottom:22px}
  .back__perks{list-style:none;font-size:16px;line-height:1.32;padding-left:16px}
  .back__perks .indent{display:block;padding-left:82px}
</style>
</head>
<body>
  <section class="card card--front" aria-label="Card front">
    <div class="front__info">
      <h1 class="front__name">Pawhaven Retreat Elmbrook</h1>
      <p class="front__owner">CT Tom Pelley</p>
      <ul class="front__contacts">
        <li>
          <svg class="contact-icon" viewBox="0 0 24 24" aria-hidden="true">
            <rect width="24" height="24" fill="var(--icon)"/>
            <path d="M8 6c1 0 2 2.5 2 3s-1 1-1 1.5 2 3.5 3.5 4c.5 0 1-1 1.5-1s3 1 3 2-1 2.5-2.5 2.5C10 18 6 13.5 6 9c0-1.5 1-3 2-3z" fill="#fff"/>
          </svg>
          <span>631-555-0192</span>
        </li>
        <li>
          <svg class="contact-icon" viewBox="0 0 24 24" aria-hidden="true">
            <rect width="24" height="24" fill="var(--icon)"/>
            <rect x="5" y="7" width="14" height="10" fill="none" stroke="#fff" stroke-width="1.5"/>
            <path d="M5 7l7 6 7-6M5 17l5-5M19 17l-5-5" fill="none" stroke="#fff" stroke-width="1.5"/>
          </svg>
          <span>hello@pawhavenretreat.com</span>
        </li>
      </ul>
    </div>
    <div class="front__photo-side">
      <div class="front__photo" role="img" aria-label="Photo of two golden Labrador puppies sitting side by side"></div>
    </div>
  </section>

  <section class="card card--back" aria-label="Card back">
    <h2 class="back__heading">As a guest at Pawhaven Retreat, your dog will get</h2>
    <ul class="back__perks">
      <li>4-star kibble</li>
      <li>Access to my in-ground pool</li>
      <li>All-natural snack selection</li>
      <li>Companionship of other retrievers including my two</li>
      <li>Full run of entire home and fenced-in backyard</li>
      <li>Photos AND videos posted to Snapgram so you can see<span class="indent">your dog having fun while away</span></li>
      <li>Toys, bones and affection</li>
    </ul>
  </section>
</body>
</html>
```